Business Card Design for BrightvaleMedia.com

--I need a business card design for my company BrightvaleMedia.com

I have attached my logo...I want the brightvale media logo on the front of the business card, and then I want The Quillstone Chief on the back of it with my information.

I would like to see a light colored background as well as a dark colored background

FRONT:
BRIGHTVALE MEDIA LOGO
248 N. Larkmoor
3rd Floor
San Diego CA 92173
www.BrightvaleMedia.com

Advanced Website & App Development
Websites, Apps, Online Voucher Systems

Leading Edge Marketing Services
SMS, VB, SMM, SEM,

BACK:
QUILLSTONE CHIEF LOGO
Dorian Pelletta
The Quillstone Chief
Call Or Text: 619-555-0148
Dorian@QuillstoneChief.example
www.QuillstoneChief.example

Target Market(s)

small business owners

Industry/Entity Type

Business Consultant

Contact Information for Business Card

FRONT:
BRIGHTVALE MEDIA LOGO
248 N. Larkmoor
3rd Floor
San Diego CA 92173
www.BrightvaleMedia.com

SMS, VB, SMM, SEM,

BACK:
QUILLSTONE CHIEF LOGO
Dorian Pelletta
The Quillstone Chief
Dorian@QuillstoneChief.example
www.QuillstoneChief.example

Requirements
Must have
• add this quote on it somewhere, anywhere,preferrably on back
• "The Fastest Way To Success Is To Take Action”
• — Dorian Pelletta, Quillstone Chief
Nice to have
• open
Should not have
• red

```html
<!DOCTYPE html>
<html lang="en">
<head>
<meta charset="utf-8">
<title>Brightvale Media – Business Cards</title>
<link href="https://fonts.googleapis.com/css2?family=Open+Sans:wght@400;600;700&display=swap" rel="stylesheet">
<style>
  :root {
    --brand-blue: #0b6fa8;
    --brand-grey: #6b6c70;
    --ink: #2b2b2b;
    --paper: #ffffff;
    --backdrop: #e9e7e4;
  }
  * { margin: 0; padding: 0; box-sizing: border-box; }
  html, body {
    width: 1200px; height: 900px; overflow: hidden;
    background: var(--backdrop);
    font-family: "Open Sans", Arial, sans-serif;
  }
  .canvas { position: relative; width: 1200px; height: 900px; }
  .card {
    position: absolute;
    background: var(--paper);
    box-shadow: 0 6px 18px rgba(0,0,0,0.18);
    overflow: hidden;
  }

  /* Back: personal card */
  .card--personal { left: 77px; top: 34px; width: 589px; height: 364px; }
  .card__bands { position: absolute; inset: 0; }
  .wordmark {
    position: absolute;
    color: var(--brand-blue);
    font-weight: 600;
    letter-spacing: 4px;
    white-space: nowrap;
    text-align: center;
    left: 0; right: 0;
  }
  .card--personal .wordmark { top: 68px; font-size: 36px; }
  .quote {
    position: absolute; left: 40px; right: 40px; top: 134px;
    text-align: center; color: var(--brand-grey);
    font-size: 14px; line-height: 20px;
  }
  .quote__attribution { display: block; font-size: 12.5px; }
  .identity {
    position: absolute; right: 314px; top: 264px;
    text-align: right; color: var(--paper);
  }
  .identity__name { font-size: 19px; font-weight: 700; line-height: 30px; }
  .identity__title { font-size: 16px; line-height: 24px; }
  .contacts {
    position: absolute; left: 294px; top: 261px;
    list-style: none; color: var(--paper); font-size: 15.5px;
  }
  .contacts li { display: flex; align-items: center; height: 21.5px; gap: 7px; }
  .contacts svg { width: 12px; height: 12px; flex: none; }

  /* Front: company card */
  .card--company { left: 388px; top: 505px; width: 567px; height: 352px; }
  .card--company .wordmark { top: 50px; font-size: 34px; }
  .services { position: absolute; left: 0; right: 0; top: 163px; color: var(--ink); font-size: 15px; }
  .service { position: relative; text-align: center; line-height: 21px; margin-bottom: 10px; padding-right: 13px; }
  .service__arrow { position: absolute; left: 104px; top: 6px; width: 20px; height: 16px; }
  .address {
    position: absolute; left: 0; right: 0; top: 274px;
    text-align: center; font-size: 15px; color: var(--ink);
  }
  .website {
    position: absolute; left: 0; right: 0; top: 299px;
    text-align: center; font-size: 15px; font-weight: 700; color: var(--brand-blue);
    padding-right: 24px;
  }
</style>
</head>
<body>
<main class="canvas">

  <section class="card card--personal" aria-label="Quillstone Chief card">
    <svg class="card__bands" width="589" height="364" viewBox="0 0 589 364" aria-hidden="true">
      <polygon points="0,199 403,199 378,226 0,226" fill="var(--brand-grey)"/>
      <polygon points="416,192 589,192 589,364 0,364 0,229 382,229" fill="var(--brand-blue)"/>
    </svg>
    <div class="wordmark">QUILLSTONE CHIEF</div>
    <p class="quote">“The Fastest Way To Success Is To Take Action”
      <span class="quote__attribution">— Dorian Pelletta, Quillstone Chief</span>
    </p>
    <div class="identity">
      <div class="identity__name">Dorian Pelletta</div>
      <div class="identity__title">The Quillstone Chief</div>
    </div>
    <ul class="contacts">
      <li>
        <svg viewBox="0 0 24 24" aria-hidden="true"><path fill="#fff" d="M6.6 10.8a15.1 15.1 0 0 0 6.6 6.6l2.2-2.2c.3-.3.7-.4 1-.2 1.1.4 2.3.6 3.6.6.6 0 1 .4 1 1V20c0 .6-.4 1-1 1A17 17 0 0 1 3 4c0-.6.4-1 1-1h3.5c.6 0 1 .4 1 1 0 1.3.2 2.5.6 3.6.1.3 0 .7-.2 1z"/></svg>
        619-555-0148
      </li>
      <li>
        <svg viewBox="0 0 24 24" aria-hidden="true"><rect x="2" y="5" width="20" height="14" rx="1" fill="#fff"/><path d="M3 6l9 7 9-7" stroke="#0b6fa8" stroke-width="1.8" fill="none"/></svg>
        Dorian@QuillstoneChief.example
      </li>
      <li>
        <svg viewBox="0 0 24 24" aria-hidden="true"><circle cx="12" cy="12" r="9.5" fill="none" stroke="#fff" stroke-width="2"/><ellipse cx="12" cy="12" rx="4" ry="9.5" fill="none" stroke="#fff" stroke-width="1.8"/><path d="M2.5 12h19M4 7.5h16M4 16.5h16" stroke="#fff" stroke-width="1.6"/></svg>
        www.QuillstoneChief.example
      </li>
    </ul>
  </section>

  <section class="card card--company" aria-label="Brightvale Media card">
    <div class="wordmark">BRIGHTVALE MEDIA</div>
    <div class="services">
      <div class="service">
        <svg class="service__arrow" viewBox="0 0 20 16" aria-hidden="true"><polygon points="0,0 20,8 0,16 5,8" fill="var(--brand-blue)"/></svg>
        Advanced Website &amp; App Development<br>Websites, Apps, Online Voucher Systems
      </div>
      <div class="service">
        <svg class="service__arrow" viewBox="0 0 20 16" aria-hidden="true"><polygon points="0,0 20,8 0,16 5,8" fill="var(--brand-blue)"/></svg>
        Leading Edge Marketing Services<br>SMS, VB, SMM, SEM,
      </div>
    </div>
    <p class="address">248 N. Larkmoor&nbsp; 3rd Floor, San Diego CA 92173</p>
    <p class="website">www.BrightvaleMedia.com</p>
  </section>

</main>
</body>
</html>
```